Web Design For Manufacturing And Outsourcing Company

Pick up the pieces from our previous developer and help us complete our website.

5 pages - Home,Machining,Sourcing,About Us, and Contact

Attached you will find screen shots of previous direction but we're open to new ideas.

We can provide all text and images needed.

Thanks!

Number of Pages Required

5+ page

```html
<!DOCTYPE html>
<html lang="en">
<head>
<meta charset="utf-8">
<title>Keel Industries</title>
<link href="https://fonts.googleapis.com/css2?family=Lato:wght@400;700;900&family=Open+Sans:wght@400;600;700&display=swap" rel="stylesheet">
<style>
:root{
  --orange:#ec4c1c;
  --orange-dark:#c43a10;
  --ink:#1d1d1d;
  --dark:#161616;
  --dark-2:#262626;
  --grey-bg:#f1f1f1;
  --text:#333;
  --muted:#777;
  --white:#fff;
  --line:#ddd;
}
*{margin:0;padding:0;box-sizing:border-box}
html,body{width:1200px;height:4800px;overflow:hidden}
body{font-family:"Open Sans",Arial,sans-serif;color:var(--text);background:var(--white)}
.page{position:relative;width:1200px;height:4800px;overflow:hidden}
.abs{position:absolute}
.center{text-align:center;left:0;width:1200px}
.h2{font-family:"Lato",Arial,sans-serif;font-weight:900;font-size:40px;letter-spacing:1px;color:var(--ink)}
.btn{position:absolute;background:var(--orange);color:var(--white);font-family:"Lato",Arial,sans-serif;font-weight:700;display:flex;align-items:center;justify-content:center;letter-spacing:1px}

/* header */
.topbar{left:390px;top:0;width:670px;height:34px}
.topbar-info{left:490px;top:0;height:32px;display:flex;gap:46px;align-items:center;color:var(--white);font-size:15px}
.topbar-info span{display:flex;align-items:center;gap:8px}
.social{display:flex;gap:4px;margin-left:-20px}
.social i{width:20px;height:20px;border:1.5px solid var(--white);border-radius:50%;display:block}
.brand{left:140px;top:12px;width:170px;text-align:center}
.brand-mark{width:44px;height:44px;background:var(--orange);margin:0 auto 8px}
.brand-name{font-family:"Lato",Arial,sans-serif;font-weight:900;font-size:14px;letter-spacing:2px;color:var(--ink)}
.nav{left:448px;top:76px;display:flex;gap:30px;font-family:"Lato",Arial,sans-serif;font-weight:700;font-size:16px;color:var(--ink)}
.nav .active{color:var(--orange);position:relative}
.nav .active:after{content:"";position:absolute;left:50%;bottom:-22px;width:8px;height:8px;background:var(--orange);transform:translateX(-50%) rotate(45deg)}

/* hero */
.hero{left:0;top:128px;width:1200px;height:580px;background:linear-gradient(135deg,#2b2b2b 0%,#6e6e6e 45%,#3a3a3a 70%,#141414 100%)}
.hero-title{top:360px;font-family:"Lato",Arial,sans-serif;font-size:72px;color:var(--white)}
.hero-sub{top:444px;font-size:22px;line-height:32px;color:#eee}
.hero-btn{left:495px;top:528px;width:210px;height:50px;font-size:18px}
.arrow{top:408px;width:22px;height:22px;border-left:2px solid #ddd;border-bottom:2px solid #ddd}

/* about */
.about-title{top:786px}
.policy{top:852px;font-size:18px;color:var(--ink)}
.about-text{left:190px;top:896px;width:820px;text-align:center;font-size:15px;line-height:37px}
.values-title{top:1070px;font-size:18px;color:var(--ink)}
.value{top:1125px;width:190px;height:155px;background:#fafafa;border:1px solid var(--line);box-shadow:0 2px 6px rgba(0,0,0,.08);text-align:center;font-size:17px;color:var(--ink)}
.value svg{margin:28px auto 10px;display:block}

/* machining */
.mach-title{top:1514px;color:var(--white)}
.mach-text{left:190px;top:1584px;width:820px;text-align:center;font-size:15px;line-height:34px;color:#eee}
.tile{width:290px;height:220px;border:2px solid #777}
.tile .photo{position:absolute;inset:0}
.tile .label{position:absolute;left:0;right:0;bottom:0;height:36px;background:var(--orange);color:var(--white);font-family:"Lato",Arial,sans-serif;font-size:17px;display:flex;align-items:center;justify-content:center}

/* sourcing */
.src-title{left:145px;top:2590px}
.src-text{left:145px;top:2652px;width:300px;font-size:15px;line-height:34px}
.src-btn{left:145px;top:2940px;width:135px;height:40px;border:2px solid var(--orange);color:var(--orange);font-size:14px;font-weight:600;display:flex;align-items:center;justify-content:center}
.card{width:262px;height:257px;background:var(--white);border:1px solid #ccc;text-align:center}
.card svg{display:block;margin:28px auto 8px}
.card h3{font-family:"Lato",Arial,sans-serif;font-size:17px;color:var(--ink);letter-spacing:1px;margin-bottom:14px}
.card p{font-size:13px;line-height:25px;padding:0 26px;color:#444}

/* testimonials */
.test-title{top:3352px;font-family:"Lato",Arial,sans-serif;font-size:40px;color:var(--white);letter-spacing:1px}
.quote{width:300px;top:3456px}
.avatar{position:absolute;left:0;top:0;width:74px;height:74px;border-radius:50%;background:linear-gradient(#b8a89a,#5d4d42);border:3px solid var(--white)}
.quote p{position:absolute;left:96px;top:0;width:200px;font-size:13px;line-height:22px;color:#eee}
.quote .name{position:absolute;left:96px;top:104px;font-style:italic;font-size:14px;color:#ddd}
.quote .stars{position:absolute;left:96px;top:130px;color:var(--orange);font-size:19px;letter-spacing:2px}
.pager{top:3656px;width:30px;height:30px;border:2px solid #ccc;border-radius:50%}

/* cta */
.cta-text{top:3910px;font-family:"Lato",Arial,sans-serif;font-weight:900;font-size:32px;line-height:52px;color:var(--ink);letter-spacing:1px}
.cta-btn{left:490px;top:4050px;width:215px;height:58px;font-size:20px}

/* partners */
.partners{left:0;top:4218px;width:1200px;height:142px;background:var(--grey-bg);display:flex;align-items:center;justify-content:center;gap:78px;font-family:"Lato",Arial,sans-serif;font-weight:900;font-size:26px;color:#999}

/* footer */
.footer{left:0;top:4360px;width:1200px;height:350px;background:#2a2a2a}
.f-brand{left:140px;top:4462px;width:130px;text-align:center}
.f-brand .brand-mark{width:56px;height:56px}
.f-brand .brand-name{color:var(--white)}
.f-head{top:4425px;font-family:"Lato",Arial,sans-serif;font-weight:900;font-size:18px;color:var(--white);letter-spacing:1px}
.f-contact{left:305px;top:4470px;width:280px;color:#ddd;font-size:14px;line-height:22px}
.f-contact div{display:flex;gap:16px;margin-bottom:18px}
.f-contact svg{flex:none;margin-top:3px}
.f-sign p{color:#ddd;font-size:13px;line-height:21px}
.f-input{left:608px;top:4528px;width:275px;height:30px;background:var(--white);border-radius:15px;font-size:12px;color:#888;padding:7px 14px}
.f-sub{left:608px;top:4573px;width:275px;height:30px;border-radius:15px;font-size:13px}
.f-links{left:950px;top:4470px;color:#ddd;font-size:15px;line-height:29px}
.copy{left:0;top:4710px;width:1200px;height:90px;background:#1c1c1c;color:#ccc;font-size:14px;display:flex;align-items:center;justify-content:center}
</style>
</head>
<body>
<div class="page">

  <!-- header -->
  <svg class="abs topbar" width="670" height="34" viewBox="0 0 670 34"><polygon points="0,0 670,0 650,34 20,34" fill="#444"/></svg>
  <div class="abs topbar-info">
    <span><svg width="14" height="14" viewBox="0 0 24 24"><path d="M6 2l4 5-2 3c1 3 3 5 6 6l3-2 5 4-3 4C10 22 2 14 2 5z" fill="#fff"/></svg>+888 4120 7700</span>
    <span><svg width="16" height="12" viewBox="0 0 16 12"><rect width="16" height="12" fill="#fff"/><path d="M0 0l8 7 8-7" stroke="#444" fill="none"/></svg>info@keel-ind.com</span>
    <span class="social"><i></i><i></i><i></i></span>
  </div>
  <div class="abs brand"><div class="brand-mark"></div><div class="brand-name">KEEL INDUSTRIES</div></div>
  <nav class="abs nav"><span class="active">HOME</span><span>ABOUT US</span><span>MACHINING</span><span>SOURCING</span><span>BLOG</span><span>CONTACT US</span></nav>

  <!-- hero -->
  <div class="abs hero" role="img" aria-label="Close-up photo of a CNC milling spindle cutting metal with coolant spray"></div>
  <div class="abs arrow" style="left:88px;transform:rotate(45deg)"></div>
  <div class="abs arrow" style="left:1090px;transform:rotate(-135deg)"></div>
  <h1 class="abs center hero-title" style="font-weight:400">Keel Industries</h1>
  <p class="abs center hero-sub">Nemo enim ipsam voluptatem quia voluptas<br>sit aspernatur aut odit aut fugit.</p>
  <div class="btn hero-btn">GET MORE INFO</div>

  <!-- about -->
  <h2 class="abs center h2 about-title">ABOUT KEEL INDUSTRIES</h2>
  <p class="abs center policy">QUALITY POLICY:</p>
  <p class="abs about-text">We are committed to consistently exceeding customer expectations by providing products, services and sourcing solutions of the highest standard of quality. With our streamlined processes our method is efficient, provides value and ensures on time delivery. Our success is based on continuously improving the efficiencies and effectiveness of our products, processes, and quality management systems.</p>
  <p class="abs center values-title">CORE VALUES</p>
  <div class="abs value" style="left:300px">
    <svg width="64" height="56" viewBox="0 0 64 56" fill="none" stroke="#333" stroke-width="2"><circle cx="32" cy="12" r="7"/><circle cx="14" cy="22" r="6"/><circle cx="50" cy="22" r="6"/><path d="M22 44v-12h20v12M4 50v-14h18M60 50v-14H42"/><path d="M20 30l-4 4M44 30l4 4" stroke="#ec4c1c"/></svg>Teamwork</div>
  <div class="abs value" style="left:505px">
    <svg width="64" height="56" viewBox="0 0 64 56" fill="none" stroke="#333" stroke-width="2"><path d="M6 30l14-14 12 8 12-8 14 14-22 18z"/><path d="M20 16l10 12M44 16l-10 12" stroke="#ec4c1c"/></svg>Respect</div>
  <div class="abs value" style="left:710px">
    <svg width="64" height="56" viewBox="0 0 64 56" fill="none" stroke="#333" stroke-width="2"><rect x="16" y="8" width="32" height="40"/><path d="M24 20h16M24 28h10"/><path d="M34 40l6 6 10-12" stroke="#ec4c1c"/></svg>Gratitude</div>

  <!-- machining -->
  <svg class="abs" style="left:0;top:1380px" width="1200" height="1040" viewBox="0 0 1200 1040">
    <polygon points="0,10 330,40 0,62" fill="#ec4c1c"/>
    <polygon points="0,62 330,40 1200,0 1200,930 0,1030" fill="#1a1a1a"/>
    <polygon points="0,0 0,80 330,40" fill="#c43a10" opacity=".7"/>
    <polygon points="900,930 1200,890 1200,985" fill="#ec4c1c"/>
  </svg>
  <div class="abs" style="left:0;top:1380px;width:1200px;height:1030px;background:linear-gradient(180deg,rgba(60,60,60,.35),rgba(0,0,0,0))" role="img" aria-label="Dim background photo of a machine shop floor"></div>
  <h2 class="abs center h2 mach-title" style="color:#fff">MACHINING</h2>
  <p class="abs mach-text">Keel Industries brings their machining knowledge to the table every day working closely with our customers to put value into each part we produce. Working as a strategic partner, Keel Industries is able to deliver precision machined components with the highest quality, on time, and at the most cost effective price.</p>

  <div class="abs tile" style="left:145px;top:1745px"><div class="photo" role="img" aria-label="Photo of multi-axis machining with coolant" style="background:linear-gradient(135deg,#c9ccd0,#6b7178)"></div><div class="label">MULTIPLE AXIS EQUIPMENT</div></div>
  <div class="abs tile" style="left:455px;top:1745px"><div class="photo" role="img" aria-label="Photo of lathe tooling measuring tolerances" style="background:linear-gradient(135deg,#8a9097,#3e4348)"></div><div class="label">TOLERANCES</div></div>
  <div class="abs tile" style="left:765px;top:1745px"><div class="photo" role="img" aria-label="Photo of custom built fixtures" style="background:linear-gradient(135deg,#7a7f8a,#2e3140)"></div><div class="label">CUSTOM BUILT FIXTURES</div></div>
  <div class="abs tile" style="left:145px;top:1985px"><div class="photo" role="img" aria-label="Photo of prototype machined parts on a sketch" style="background:linear-gradient(135deg,#e2e4e6,#9ea3a8)"></div><div class="label">PROTOTYPES TO PRODUCTION</div></div>
  <div class="abs tile" style="left:455px;top:1985px"><div class="photo" role="img" aria-label="Photo of machined assemblies" style="background:linear-gradient(135deg,#5e6266,#1e2022)"></div><div class="label">ASSEMBLIES</div></div>
  <div class="abs tile" style="left:765px;top:1985px"><div class="photo" role="img" aria-label="Photo of coordinate measuring machine probe" style="background:linear-gradient(135deg,#b4b8bc,#54585c)"></div><div class="label">CMM</div></div>

  <!-- sourcing -->
  <div class="abs" style="left:0;top:2400px;width:1200px;height:830px;background:var(--grey-bg)"></div>
  <svg class="abs" style="left:0;top:2300px" width="1200" height="130" viewBox="0 0 1200 130"><polygon points="0,110 1200,10 1200,85 0,130" fill="#1a1a1a"/><polygon points="900,40 1200,10 1200,80" fill="#ec4c1c"/></svg>
  <h2 class="abs h2 src-title">SOURCING</h2>
  <p class="abs src-text">Over the years we identified the need to provide one stop services to purchasing departments. We have built an extensive network of hard to find products, machining specialists and leveraging open machine time to provide the most economical alternatives to our customers. We have developed a specialized</p>
  <div class="abs src-btn">READ MORE</div>

  <div class="abs card" style="left:505px;top:2515px">
    <svg width="60" height="50" viewBox="0 0 60 50" fill="none" stroke="#ec4c1c" stroke-width="2"><circle cx="30" cy="22" r="12"/><circle cx="30" cy="22" r="4"/><path d="M30 4v6M30 34v6M12 22h6M42 22h6"/><path d="M8 46h44" stroke="#333"/></svg>
    <h3>VETTING</h3><p>Qualifying suppliers is something we take as seriously as you do. We conduct a thorough audit and background check for every</p></div>
  <div class="abs card" style="left:793px;top:2515px">
    <svg width="60" height="50" viewBox="0 0 60 50" fill="none" stroke="#ec4c1c" stroke-width="2"><rect x="16" y="6" width="28" height="40" rx="2"/><rect x="24" y="2" width="12" height="7" fill="#fff"/><circle cx="30" cy="24" r="7"/><path d="M22 38h16" stroke="#333"/></svg>
    <h3>QUALITY</h3><p>Parts are 100% inspected. If any problems arise, there's no question about what happens next - you still get the parts you need</p></div>
  <div class="abs card" style="left:505px;top:2795px">
    <svg width="60" height="50" viewBox="0 0 60 50" fill="none" stroke="#ec4c1c" stroke-width="2"><rect x="6" y="6" width="18" height="14"/><rect x="36" y="6" width="18" height="14"/><rect x="21" y="30" width="18" height="14"/><path d="M15 20v8h30v-8M30 28v2" stroke="#333"/></svg>
    <h3>PROCESS</h3><p>Ease of ordering and transparency throughout the assignment with communication and tracking of order status.</p></div>
  <div class="abs card" style="left:793px;top:2795px">
    <svg width="60" height="50" viewBox="0 0 60 50" fill="#ec4c1c"><rect x="10" y="32" width="7" height="14"/><rect x="21" y="26" width="7" height="20"/><rect x="32" y="20" width="7" height="26"/><rect x="43" y="12" width="7" height="34"/><path d="M8 22L24 12l10 4 16-12" stroke="#333" stroke-width="2" fill="none"/></svg>
    <h3>BENEFITS</h3><p>Existing Relationships Supply base knowledge. Nemo enim ipsam voluptatem quia voluptas sit</p></div>

  <!-- testimonials -->
  <svg class="abs" style="left:0;top:3200px" width="1200" height="670" viewBox="0 0 1200 670">
    <polygon points="0,10 1200,55 1200,580 0,670" fill="#1a1a1a"/>
    <polygon points="0,10 420,30 0,100" fill="#ec4c1c"/>
    <polygon points="880,600 1200,560 1200,620" fill="#ec4c1c"/>
  </svg>
  <div class="abs" style="left:0;top:3260px;width:1200px;height:560px;background:linear-gradient(90deg,rgba(70,70,70,.3),rgba(0,0,0,0))" role="img" aria-label="Dim background photo of an industrial workshop"></div>
  <h2 class="abs center test-title" style="font-weight:400">WHAT OUR CLIENTS SAY</h2>

  <div class="abs quote" style="left:145px"><div class="avatar" role="img" aria-label="Client portrait"></div><p>“ Sed vero eos et accusamus et iusto odio dignissimos ducimus qui blanditiis praesentium volum deleniti atque corrupti</p><span class="name">Owen Marsh</span><span class="stars">★★★★☆</span></div>
  <div class="abs quote" style="left:455px"><div class="avatar" role="img" aria-label="Client portrait"></div><p>“ Sed vero eos et accusamus et iusto odio dignissimos ducimus qui blanditiis praesentium volum deleniti atque corrupti</p><span class="name">Owen Marsh</span><span class="stars">★★★★☆</span></div>
  <div class="abs quote" style="left:770px"><div class="avatar" role="img" aria-label="Client portrait"></div><p>“ Sed vero eos et accusamus et iusto odio dignissimos ducimus qui blanditiis praesentium volum deleniti atque corrupti</p><span class="name">Owen Marsh</span><span class="stars">★★★★☆</span></div>
  <div class="abs pager" style="left:566px"></div>
  <div class="abs pager" style="left:602px"></div>

  <!-- call to action -->
  <p class="abs center cta-text">CONTACT US TODAY WITH YOUR MACHINING<br>OR SOURCING NEEDS!</p>
  <div class="btn cta-btn">GET IN TOUCH</div>

  <!-- partners -->
  <div class="abs partners"><span>Torvik</span><span>Alvena</span><span>Stenmark</span><span>Brisa</span><span>Verdal</span><span>Calbrook</span></div>

  <!-- footer -->
  <div class="abs footer"></div>
  <div class="abs f-brand"><div class="brand-mark"></div><div class="brand-name">KEEL INDUSTRIES</div></div>
  <h4 class="abs f-head" style="left:305px">CONTACT US</h4>
  <div class="abs f-contact">
    <div><svg width="14" height="18" viewBox="0 0 14 18"><path d="M7 1a6 6 0 0 1 6 6c0 4-6 10-6 10S1 11 1 7a6 6 0 0 1 6-6z" fill="none" stroke="#ddd" stroke-width="1.5"/><circle cx="7" cy="7" r="2" fill="#ddd"/></svg><span>Keel Industries<br>1250 Ridge Rd. Fairview<br>Heights, MI 48000</span></div>
    <div><svg width="14" height="14" viewBox="0 0 24 24"><path d="M6 2l4 5-2 3c1 3 3 5 6 6l3-2 5 4-3 4C10 22 2 14 2 5z" fill="none" stroke="#ddd" stroke-width="2"/></svg><span>Phone: 313 555 0142</span></div>
    <div><svg width="16" height="12" viewBox="0 0 16 12"><rect x=".5" y=".5" width="15" height="11" fill="none" stroke="#ddd"/><path d="M.5.5l7.5 6 7.5-6" stroke="#ddd" fill="none"/></svg><span>Email: info@keel-ind.com</span></div>
  </div>
  <h4 class="abs f-head" style="left:608px">SIGN UP TO RECEIVE EMAIL</h4>
  <div class="abs f-sign" style="left:608px;top:4460px;width:290px"><p>Excepteur sint occaecat cupidatat non proident, sunt in culpa qui labore</p></div>
  <div class="abs f-input">Enter Email</div>
  <div class="btn f-sub">SUBSCRIBE</div>
  <h4 class="abs f-head" style="left:950px">QUICK LINKS</h4>
  <div class="abs f-links">Home<br>About Us<br>Machining<br>Sourcing<br>Blog<br>Contact Us</div>
  <div class="abs copy">Copyright © Keel Industries 2019. All rights reserved.</div>
</div>
</body>
</html>
```